Bram Keystone Homes needs a business card

We need a business card for a new company in Canada, Ontario. Our company is all about luxury contraction homes for our clients. Our product and services are custom projects design. Under the business logo that will be created, we want a slogan that will be a memorable phrase for consumers to remember us to tell their friends and relatives.

Additional infomation
- Ludovic Entrasse
- President / Ceo
-519.604.3087

Find point what luxury construction products and services can be done

We like to see colors:
- #663300
- and something other colors or color that would attract the client needs and wants

The final design should communicate leads from new or old clients that will grow our empire. Most of all, we try to work among the budget that clients want

NOTE
- we also need an icon for the business (Example: Instagram, Facebook, and Whatsapp icons)
- We want the company name to be remembered easily for clients and our distributors who would get our orders.
- we need an icon on the business cards: Facebook and Instagram.

Thanks,
Bram Keystone Homes

```html
<!DOCTYPE html>
<html lang="en">
<head>
<meta charset="utf-8">
<title>Bram Keystone Homes — Business Card</title>
<link rel="stylesheet" href="https://fonts.googleapis.com/css2?family=Poppins:wght@400;500;800&family=Roboto+Condensed:wght@700&display=swap">
<style>
  :root {
    --brown: #663300;
    --paper: #ffffff;
    --pattern-light: #f6f3ef;
    --pattern-mid: #ece6df;
    --backdrop: #e4e1dd;
    --band-text: #ffffff;
  }
  * { box-sizing: border-box; margin: 0; padding: 0; }
  html, body {
    width: 1200px; height: 874px; overflow: hidden;
    background: var(--backdrop);
  }
  .canvas {
    position: relative; width: 1200px; height: 874px;
  }
  .card {
    position: absolute; left: 330px; width: 540px; height: 309px;
    background: var(--paper);
    box-shadow: 0 6px 18px rgba(0,0,0,0.18);
    overflow: hidden;
  }
  .card-front { top: 108px; }
  .card-back { top: 457px; }

  .brand {
    position: absolute; top: 96px; left: 0; right: 0;
    text-align: center; color: var(--brown);
  }
  .brand-name {
    font-family: "Poppins", sans-serif; font-weight: 800;
    font-size: 38px; line-height: 1; letter-spacing: -0.5px;
  }
  .brand-tagline {
    margin-top: 8px;
    font-family: "Roboto Condensed", sans-serif; font-weight: 700;
    font-size: 13.5px; letter-spacing: 0.4px;
  }
  .social {
    position: absolute; top: 205px; left: 0; right: 0;
    display: flex; justify-content: center; gap: 4px;
  }
  .social svg { width: 26px; height: 26px; }

  .pattern-field {
    position: absolute; inset: 0;
    background: linear-gradient(135deg, var(--pattern-light), var(--pattern-mid) 50%, var(--pattern-light));
  }
  .contact-band {
    position: absolute; left: 0; right: 0; top: 140px; height: 96px;
    background: var(--brown); color: var(--band-text);
    font-family: "Poppins", sans-serif;
  }
  .person {
    position: absolute; right: 270px; top: 22px; text-align: right;
  }
  .person-name { font-size: 20px; font-weight: 500; line-height: 1.2; }
  .person-title { font-size: 15px; font-weight: 400; line-height: 1.3; }
  .divider {
    position: absolute; left: 288px; top: 18px; width: 2px; height: 60px;
    background: var(--band-text);
  }
  .phone {
    position: absolute; left: 312px; top: 34px;
    font-size: 20px; font-weight: 500; letter-spacing: 0.5px;
  }
</style>
</head>
<body>
<main class="canvas">
  <section class="card card-front">
    <div class="brand">
      <div class="brand-name">Bram Keystone Homes</div>
      <div class="brand-tagline">- HOME RENOVATIONS - CUSTOM PROJECT DESIGN -</div>
    </div>
    <div class="social" aria-label="Social media links">
      <svg viewBox="0 0 26 26" role="img" aria-label="Social profile"><circle cx="13" cy="13" r="11.5" fill="none" stroke="#663300" stroke-width="1"/></svg>
      <svg viewBox="0 0 26 26" role="img" aria-label="Social profile"><circle cx="13" cy="13" r="11.5" fill="none" stroke="#663300" stroke-width="1"/></svg>
      <svg viewBox="0 0 26 26" role="img" aria-label="Messaging contact"><circle cx="13" cy="13" r="11.5" fill="none" stroke="#663300" stroke-width="1"/></svg>
    </div>
  </section>

  <section class="card card-back">
    <div class="pattern-field" role="img" aria-label="Faint repeated company name pattern"></div>
    <div class="contact-band">
      <div class="person">
        <div class="person-name">Ludovic Entrasse</div>
        <div class="person-title">President / Ceo</div>
      </div>
      <div class="divider"></div>
      <div class="phone">519.604.3087</div>
    </div>
  </section>
</main>
</body>
</html>
```